We are a company with over 35 years experience supporting our customers IT needs. Implementing wa..*

We want customers to see a strong product line that is covered by our sales and service team.

We sell and service Impact, Mobile and thermal printers. We sell and support fiber optics, data cabling and wireless communications. We manufacture rack labels for warehouse distribution centers and also make shipping labels and private custom labels and all barcode scanning equipment used for receiving, picking and inventory control. We have custom software solutions for WMS and DIstribution Centers.

We support customers like Brindlecart, Fizzora Pop, Bunwise Grill, Vemaru, Supermarket chains and 3PL companies.

Looking for a modern design to attract customer who purchase brands we distribute and support. Products from Glyphworks, KDW, Scrivel Mobile, RENU, Optivane Scanners, Halvorn Networking Equipment to name a few.

Target Market(s)

3PL, Distribution, Bottling Companies, Supermarket Chains, Pharmaceutical

Coding

Coded - Design and coding required

Number of Pages Required

2 page

Colors

Designer to choose colors to be used in the design.

Requirements
Must have
• Warehouse Environment or Distribution Center feel.
Nice to have
• Brands we support
Should not have
• Online store feel

```html
<!DOCTYPE html>
<html lang="en">
<head>
<meta charset="utf-8">
<title>Tarnell Holding Group</title>
<link href="https://fonts.googleapis.com/css2?family=Libre+Franklin:wght@400;500;600;700;800&family=Open+Sans:wght@400;600&display=swap" rel="stylesheet">
<style>
:root{
  --orange:#e8561c;
  --green:#2e6b3c;
  --ink:#1b1b1b;
  --text:#555;
  --light:#f3f3f3;
  --footer:#1c1d20;
}
*{margin:0;padding:0;box-sizing:border-box}
html,body{width:1200px;height:4858px;overflow:hidden;background:#fff}
body{position:relative;font-family:"Open Sans",sans-serif;color:var(--text)}
.abs{position:absolute}
h1,h2,h3,.head{font-family:"Libre Franklin",sans-serif;color:var(--ink)}
.btn{position:absolute;display:flex;align-items:center;justify-content:center;gap:8px;background:var(--orange);color:#fff;border-radius:22px;font:700 14px "Libre Franklin",sans-serif;letter-spacing:.3px;box-shadow:0 3px 6px rgba(0,0,0,.15)}
.btn svg{width:12px;height:12px}
.rule{position:absolute;height:4px;width:72px;background:var(--green)}

/* header */
.site-header{position:absolute;left:0;top:0;width:1200px;height:111px;background:#fff;z-index:2}
.brand{left:143px;top:30px;display:flex;align-items:center;gap:10px;font:800 32px "Libre Franklin",sans-serif;color:var(--green)}
.brand .dot{width:16px;height:16px;border-radius:50%;background:var(--orange)}
.brand small{font-size:20px;color:var(--orange);font-weight:800;margin-left:6px}
.contact-top{top:20px;display:flex;align-items:center;gap:10px;font:600 17px "Libre Franklin",sans-serif;color:var(--green)}
.contact-top i{width:30px;height:30px;border-radius:50%;background:var(--orange);display:flex;align-items:center;justify-content:center}
.nav{top:73px;left:428px;display:flex;gap:26px;font:600 14px "Libre Franklin",sans-serif;color:var(--ink)}
.nav .on{color:var(--orange)}

/* hero */
.hero{left:0;top:111px;width:1200px;height:653px;background:linear-gradient(100deg,#9a5a2c 0%,#c06a2b 30%,#7a8040 60%,#4f7f45 100%)}
.hero-shade{left:0;top:111px;width:700px;height:653px;background:linear-gradient(90deg,rgba(90,40,10,.35),rgba(0,0,0,0))}
.hero-title{left:145px;top:312px;color:#fff;font-size:50px;font-weight:700}
.hero-text{left:145px;top:390px;width:460px;color:#fff;font:600 17px/29px "Libre Franklin",sans-serif}
.dots{left:148px;top:570px;display:flex;gap:10px;align-items:center}
.dots span{width:12px;height:12px;border-radius:50%;background:#fff}
.dots .cur{width:22px;height:22px;border:2px solid #fff;background:transparent;position:relative}
.dots .cur::after{content:"";position:absolute;inset:4px;border-radius:50%;background:#fff}

/* welcome */
.welcome-frame{left:164px;top:862px;width:361px;height:365px;border:3px solid var(--green)}
.welcome-img{left:147px;top:877px;width:366px;height:359px;background:linear-gradient(135deg,#e9744a 0%,#c88f7a 35%,#6f88a8 70%,#2f4a6e 100%)}
.eyebrow{left:568px;top:873px;font:500 24px "Libre Franklin",sans-serif;color:var(--orange)}
.welcome h2{left:568px;top:906px;font-size:37px;font-weight:700}
.welcome p{left:568px;top:996px;width:490px;font-size:13px;line-height:25.5px}

/* services */
.services-bg{left:0;top:1340px;width:1200px;height:679px;background:linear-gradient(135deg,#e4ecf1 0%,#f4f7f9 45%,#dfe8ee 100%)}
.services h2{left:143px;top:1464px;font-size:38px;line-height:42px;font-weight:800;text-transform:uppercase}
.services .intro{left:143px;top:1600px;width:285px;font-size:13px;line-height:23.5px}
.svc{position:absolute;width:287px;height:204px;background:#f7f7f7;border:1px solid #dcdcdc;box-shadow:0 2px 6px rgba(0,0,0,.08);padding:26px 22px}
.svc .top{display:flex;align-items:center;gap:14px;height:60px}
.svc .ico{width:64px;height:64px;border-radius:50%;background:var(--orange);flex:none;display:flex;align-items:center;justify-content:center}
.svc h3{font-size:18px;line-height:26px;font-weight:600;white-space:nowrap}
.svc p{margin-top:20px;font-size:13px;line-height:24px}

/* products */
.products-band{left:0;top:2019px;width:1200px;height:438px;background:var(--green)}
.products h2{left:0;width:1200px;text-align:center;top:2110px;color:#fff;font-size:38px;font-weight:800}
.card{position:absolute;width:285px;height:353px;background:#f7f7f7;border:1px solid #e1e1e1;box-shadow:0 2px 8px rgba(0,0,0,.1);text-align:center}
.card .pic{height:219px;background:#fff;display:flex;align-items:center;justify-content:center}
.card .pic div{width:150px;height:150px;border-radius:10px;background:linear-gradient(160deg,#4a4a4a,#161616)}
.card h3{margin-top:20px;font-size:19px;font-weight:500}
.card p{margin:12px auto 0;width:240px;font-size:13px;line-height:21px}

/* customers */
.customers h2{left:0;width:1200px;text-align:center;top:3304px;font-size:38px;font-weight:800}
.logo{position:absolute;top:3414px;width:176px;height:77px;background:#fff;border:1px solid #ddd;display:flex;align-items:center;justify-content:center;gap:8px;font:700 19px "Libre Franklin",sans-serif;color:var(--green)}
.logo i{width:12px;height:12px;background:var(--orange);border-radius:50%}

/* blog */
.blog h2{left:0;width:1200px;text-align:center;top:3712px;font-size:38px;font-weight:800}
.post{position:absolute;top:3834px;width:288px;height:386px;border:1px solid #ddd;box-shadow:0 2px 6px rgba(0,0,0,.08);background:#fff}
.post .pic{height:185px}
.post h3{margin:20px 18px 0;font-size:15px;line-height:23px;font-weight:600}
.post .date{margin:12px 18px 0;display:flex;align-items:center;gap:10px;font:700 13px "Libre Franklin",sans-serif;color:var(--orange)}
.post .date i{width:24px;height:24px;border-radius:50%;background:var(--orange);display:flex;align-items:center;justify-content:center}
.post p{margin:14px 18px 0;font-size:13px;line-height:23px}

/* footer */
.footer h4{position:absolute;top:4440px;font:700 18px "Libre Franklin",sans-serif;color:#fff}
.f-info{left:145px;top:4490px;color:#ddd;font-size:13px;line-height:21px}
.f-info .row{display:flex;gap:14px;margin-bottom:12px}
.f-info svg{flex:none;margin-top:3px}
.links{left:464px;top:4488px;color:#ddd;font-size:13px;line-height:27.5px}
.quote-note{left:668px;top:4492px;color:#ddd;font-size:13px}
.field{position:absolute;height:40px;border:1px solid #bbb;color:#ddd;font-size:12px;padding:11px 12px}
.submit{position:absolute;left:668px;top:4642px;width:209px;height:36px;background:var(--orange);color:#fff;font:700 14px "Libre Franklin",sans-serif;display:flex;align-items:center;justify-content:center}
.copy{left:0;top:4770px;width:1200px;height:88px;background:#141517;color:#ccc;font-size:13px;display:flex;align-items:center;justify-content:center}
</style>
</head>
<body>

<header class="site-header">
  <div class="abs brand"><span class="dot"></span>Tarnell<small>Holding Group</small></div>
  <div class="abs contact-top" style="left:568px"><i><svg width="14" height="14" viewBox="0 0 24 24"><path fill="#fff" d="M6.6 10.8a15 15 0 0 0 6.6 6.6l2.2-2.2c.3-.3.7-.4 1-.2 1.1.4 2.3.6 3.6.6.6 0 1 .4 1 1V20c0 .6-.4 1-1 1A17 17 0 0 1 3 4c0-.6.4-1 1-1h3.5c.6 0 1 .4 1 1 0 1.3.2 2.5.6 3.6.1.3 0 .7-.2 1z"/></svg></i>1-855-555-0142</div>
  <div class="abs contact-top" style="left:776px"><i><svg width="14" height="14" viewBox="0 0 24 24"><path fill="#fff" d="M3 5h18v14H3z M3 5l9 7 9-7"/></svg></i>info@tarnellholding.com</div>
  <nav class="abs nav"><span class="on">HOME</span><span>ABOUT US</span><span>OUR PRODUCTS</span><span>OUR CUSTOMERS</span><span>NEWS</span><span>CONTACT</span></nav>
</header>

<section class="hero-wrap">
  <div class="abs hero" role="img" aria-label="Server rack with network cabling in a data room, warm orange and green tint"></div>
  <div class="abs hero-shade"></div>
  <svg class="abs" style="left:0;top:111px" width="1200" height="653" viewBox="0 0 1200 653">
    <path d="M0 587 C250 660 520 670 760 600 C950 545 1100 460 1200 430 L1200 653 L0 653Z" fill="#fff"/>
    <path d="M700 625 C900 560 1080 480 1200 420 L1200 445 C1090 500 920 575 760 612Z" fill="#e8561c"/>
  </svg>
  <h1 class="abs hero-title">Tarnell Holding Group</h1>
  <p class="abs hero-text">Sed ut perspiciatis unde omnis iste natus error sit voluptatem accusantium doloremque laudantium, totam rem aperiam, eaque ipsa</p>
  <div class="btn" style="left:145px;top:500px;width:213px;height:40px">FIND OUT MORE <svg viewBox="0 0 12 12"><path d="M1 6h9M6 2l4 4-4 4" stroke="#fff" stroke-width="2" fill="none"/></svg></div>
  <div class="abs dots"><span class="cur"></span><span></span><span></span><span></span></div>
</section>

<section class="welcome">
  <div class="abs welcome-frame"></div>
  <div class="abs welcome-img" role="img" aria-label="Businessman holding a tablet over a city skyline"></div>
  <div class="abs eyebrow">WELCOME TO</div>
  <h2 class="abs">Tarnell Holding Group</h2>
  <div class="rule" style="left:568px;top:972px;width:62px"></div>
  <p class="abs">Sed ut perspiciatis unde omnis iste natus error sit voluptatem accuntium doloremque laudantium, totam rem aperiam, eaque ipsa quae ab illo inore veritatis et quasi architecto beatae vitae dicta sunt explicabo. Nemo enim ipsam voluptatem quia voluptas sit aspernatur aut odit aut fugit, sed quia consequuntur magni dolores eos qui ratione voluptatem sequi nesciunt. Neque porro quisquam est, qui dolorem ipsum quia dolor</p>
  <div class="btn" style="left:568px;top:1178px;width:174px;height:41px">LEARN MORE <svg viewBox="0 0 12 12"><path d="M1 6h9M6 2l4 4-4 4" stroke="#fff" stroke-width="2" fill="none"/></svg></div>
</section>

<section class="services">
  <div class="abs services-bg" role="img" aria-label="Soft blue fiber optic light strands"></div>
  <h2 class="abs">Our<br>Services</h2>
  <div class="rule" style="left:143px;top:1576px"></div>
  <p class="abs intro">Sed ut perspiciatis unde omnis iste natus error sit voluptatem accusantium doloremque laudantium, totam rem aperiam, eaque ipsa quae ab illo inventore veritatis et quasi architecto beatae vitae dicta sunt explicabo. Nemo enim ipsam voluptatem quia voluptas sit aspernatur aut odit aut fugit, sed quia</p>
  <div class="btn" style="left:143px;top:1813px;width:174px;height:40px">LEARN MORE <svg viewBox="0 0 12 12"><path d="M1 6h9M6 2l4 4-4 4" stroke="#fff" stroke-width="2" fill="none"/></svg></div>

  <div class="svc" style="left:460px;top:1447px"><div class="top"><span class="ico"><svg width="30" height="30" viewBox="0 0 30 30" fill="none" stroke="#fff" stroke-width="2"><rect x="5" y="14" width="20" height="10"/><path d="M9 14V6M13 14V6M17 14V6M21 14V6"/></svg></span><h3>Support<br>Fiber Optics</h3></div><p>Sed ut perspiciatis unde omnis iste natus sit voluptatem accusantium doloremque laium, totam</p></div>
  <div class="svc" style="left:768px;top:1447px"><div class="top"><span class="ico"><svg width="30" height="30" viewBox="0 0 30 30" fill="none" stroke="#fff" stroke-width="2"><circle cx="15" cy="15" r="10"/><circle cx="15" cy="15" r="5"/><circle cx="15" cy="15" r="1.5" fill="#fff"/></svg></span><h3>Data<br>Cabling</h3></div><p>Sed ut perspiciatis unde omnis iste natus sit voluptatem accusantium doloremque laium, totam</p></div>
  <div class="svc" style="left:460px;top:1670px"><div class="top"><span class="ico"><svg width="30" height="30" viewBox="0 0 30 30" fill="none" stroke="#fff" stroke-width="2"><rect x="6" y="6" width="18" height="18" rx="2"/><path d="M10 12h10M10 16h10M10 20h6"/></svg></span><h3>Wireless<br>Communications</h3></div><p>Sed ut perspiciatis unde omnis iste natus sit voluptatem accusantium doloremque laium, totam</p></div>
  <div class="svc" style="left:768px;top:1670px"><div class="top"><span class="ico"><svg width="30" height="30" viewBox="0 0 30 30" fill="none" stroke="#fff" stroke-width="2"><circle cx="15" cy="15" r="4"/><path d="M15 4v5M15 21v5M4 15h5M21 15h5M7 7l3.5 3.5M19.5 19.5L23 23M23 7l-3.5 3.5M10.5 19.5L7 23"/></svg></span><h3>Custom Software<br>Solutions</h3></div><p>Sed ut perspiciatis unde omnis iste natus sit voluptatem accusantium doloremque laium, totam</p></div>
</section>

<section class="products">
  <div class="abs products-band"></div>
  <h2 class="abs">OUR PRODUCTS</h2>
  <div class="abs" style="left:562px;top:2174px;width:76px;height:4px;background:#fff"></div>

  <div class="card" style="left:143px;top:2253px"><div class="pic"><div role="img" aria-label="Enclosed pedestal line printer"></div></div><h3>G8200 Enclosed Pedestal</h3><p>Sed ut perspiciatis unde omnis iste natus sit voluptatem accusantium doloremque laudantium</p></div>
  <div class="card" style="left:457px;top:2253px"><div class="pic"><div role="img" aria-label="Industrial barcode label printer"></div></div><h3>Industrial Barcode Printers</h3><p>Sed ut perspiciatis unde omnis iste natus sit voluptatem accusantium doloremque laudantium</p></div>
  <div class="card" style="left:770px;top:2253px"><div class="pic"><div role="img" aria-label="Mobile portable receipt printer"></div></div><h3>Mobile Portable Printers</h3><p>Sed ut perspiciatis unde omnis iste natus sit voluptatem accusantium doloremque laudantium</p></div>
  <div class="card" style="left:143px;top:2646px"><div class="pic"><div role="img" aria-label="Countertop barcode scanner"></div></div><h3>Optivane 3400VX</h3><p>Sed ut perspiciatis unde omnis iste natus sit voluptatem accusantium doloremque laudantium</p></div>
  <div class="card" style="left:457px;top:2646px"><div class="pic"><div role="img" aria-label="Printer mechanism spare parts"></div></div><h3>Spare Parts</h3><p>Sed ut perspiciatis unde omnis iste natus sit voluptatem accusantium doloremque laudantium</p></div>
  <div class="card" style="left:770px;top:2646px"><div class="pic"><div role="img" aria-label="Handheld mobile barcode printer"></div></div><h3>Mobile Barcode Printers</h3><p>Sed ut perspiciatis unde omnis iste natus sit voluptatem accusantium doloremque laudantium</p></div>

  <div class="btn" style="left:470px;top:3068px;width:258px;height:38px">VIEW MORE PRODUCTS <svg viewBox="0 0 12 12"><path d="M1 6h9M6 2l4 4-4 4" stroke="#fff" stroke-width="2" fill="none"/></svg></div>
</section>

<section class="customers">
  <svg class="abs" style="left:0;top:3176px" width="1200" height="420" viewBox="0 0 1200 420"><path d="M0 107 L1200 0 L1200 419 L0 372Z" fill="#f3f3f3"/></svg>
  <h2 class="abs">OUR CUSTOMERS</h2>
  <div class="rule" style="left:562px;top:3366px;width:76px"></div>
  <svg class="abs" style="left:86px;top:3436px" width="16" height="32" viewBox="0 0 16 32"><path d="M14 2L2 16l12 14" stroke="#bbb" stroke-width="2" fill="none"/></svg>
  <svg class="abs" style="left:1090px;top:3436px" width="16" height="32" viewBox="0 0 16 32"><path d="M2 2l12 14L2 30" stroke="#bbb" stroke-width="2" fill="none"/></svg>
  <div class="logo" style="left:132px">Brindlecart<i></i></div>
  <div class="logo" style="left:323px">Fizzora Pop</div>
  <div class="logo" style="left:513px">Bunwise Grill</div>
  <div class="logo" style="left:702px"><i></i>Vemaru</div>
  <div class="logo" style="left:892px"><i></i>Stackway 3PL</div>
</section>

<section class="blog">
  <h2 class="abs">LATEST BLOG</h2>
  <div class="rule" style="left:562px;top:3774px;width:76px"></div>
  <article class="post" style="left:143px"><div class="pic" role="img" aria-label="Technician working on network server cabling" style="background:linear-gradient(135deg,#3b6b8a,#1f3550 60%,#4d8a4a)"></div><h3>Nemo Enim Ipsam Voluptatem Quia Voluptas Sit</h3><div class="date"><i><svg width="12" height="12" viewBox="0 0 12 12" fill="none" stroke="#fff" stroke-width="1.5"><rect x="1" y="2" width="10" height="9"/><path d="M1 5h10"/></svg></i>JAN 15,2020</div><p>Sed ut perspiciatis unde omnis iste natus error sit voluptatem accusantium doloque laium, totam rem aperiam</p></article>
  <article class="post" style="left:455px"><div class="pic" role="img" aria-label="City at night with glowing network connections" style="background:linear-gradient(180deg,#2a4a7a,#6a5a7a 55%,#d08a3a)"></div><h3>Nemo Enim Ipsam Voluptatem Quia Voluptas Sit</h3><div class="date"><i><svg width="12" height="12" viewBox="0 0 12 12" fill="none" stroke="#fff" stroke-width="1.5"><rect x="1" y="2" width="10" height="9"/><path d="M1 5h10"/></svg></i>JAN 15,2020</div><p>Sed ut perspiciatis unde omnis iste natus error sit voluptatem accusantium doloque laium, totam rem aperiam</p></article>
  <article class="post" style="left:766px"><div class="pic" role="img" aria-label="Hands typing on a laptop beside code screens" style="background:linear-gradient(135deg,#d8dde2,#8a949e 50%,#2f3338)"></div><h3>Nemo Enim Ipsam Voluptatem Quia Voluptas Sit</h3><div class="date"><i><svg width="12" height="12" viewBox="0 0 12 12" fill="none" stroke="#fff" stroke-width="1.5"><rect x="1" y="2" width="10" height="9"/><path d="M1 5h10"/></svg></i>JAN 15,2020</div><p>Sed ut perspiciatis unde omnis iste natus error sit voluptatem accusantium doloque laium, totam rem aperiam</p></article>
</section>

<footer class="footer">
  <svg class="abs" style="left:0;top:4320px" width="1200" height="450" viewBox="0 0 1200 450">
    <path d="M0 80 C300 -10 700 -10 1000 40 C1090 55 1150 80 1200 100 L1200 450 L0 450Z" fill="#1c1d20"/>
    <path d="M880 22 C1000 30 1110 60 1200 100 L1200 120 C1110 80 1000 45 880 22Z" fill="#e8561c"/>
  </svg>
  <h4 style="left:145px">CONTACT US</h4>
  <h4 style="left:464px">QUICK LINKS</h4>
  <h4 style="left:668px">REQUEST A QUOTE</h4>
  <div class="abs f-info">
    <div class="row"><svg width="16" height="18" viewBox="0 0 16 18" fill="none" stroke="#ccc" stroke-width="1.5"><path d="M8 17s6-6 6-10A6 6 0 0 0 2 7c0 4 6 10 6 10z"/><circle cx="8" cy="7" r="2"/></svg><span>Tarnell Holding Group<br>48 Alder Ridge Rd. Fernley,<br>NV, 89408</span></div>
    <div class="row"><svg width="16" height="16" viewBox="0 0 24 24"><path fill="none" stroke="#ccc" stroke-width="1.8" d="M6.6 10.8a15 15 0 0 0 6.6 6.6l2.2-2.2 4.6 1.1V20A17 17 0 0 1 3 4h3.5l1.1 4.6z"/></svg><span>Phone:<br>808-555-0193</span></div>
    <div class="row"><svg width="16" height="14" viewBox="0 0 16 14" fill="none" stroke="#ccc" stroke-width="1.5"><rect x="1" y="1" width="14" height="12"/><path d="M1 1l7 6 7-6"/></svg><span>Email:<br>info@tarnellholding.com</span></div>
  </div>
  <div class="abs links">Home<br>About Us<br>Services<br>Products<br>News And Events<br>Shop<br>Contact</div>
  <div class="abs quote-note">Alternatively You Can Fill In The Following Contact Form:</div>
  <div class="field" style="left:668px;top:4530px;width:187px">Name</div>
  <div class="field" style="left:864px;top:4530px;width:187px">E - Mail</div>
  <div class="field" style="left:668px;top:4578px;width:187px">Subject</div>
  <div class="field" style="left:864px;top:4578px;width:187px">Message</div>
  <div class="submit">SUBMIT</div>
  <div class="abs copy">(c) 2020 Tarnell Holding Group | All Rights Reserved | Disclaimer</div>
</footer>

</body>
</html>
```